Help design website for "Brightwater Civic Advisors" to advance the common good

Here is the Google doc link that lays out the design:

https://files.plumrivet.example/sheet/d/7QmTzR2wLx9KpVbN4hJcY8sEaUoFdG3iXkMnPq5rWt6/edit?usp=sharing

Here is the Google drive folder with the logos and photos: https://vault.plumrivet.example/open?id=4HkWp9LzQe2TxRvN8mBaYc3DsUoJfG6

The testimonials are being gathered and will be shared by Friday, 1/4.

The winner will also have to migrate the coding files to my hosting site.

Thank you for your help! Looking forward to seeing your designs.

Target Market(s)

Prospective clients

Industry/Entity Type

Non Profit

Coding

Coded - Design and coding required

Number of Pages Required

5+ page

Requirements
Must have
• Noted in the Google doc regarding layout.
Nice to have

```html
<!DOCTYPE html>
<html lang="en">
<head>
<meta charset="utf-8">
<title>Brightwater Civic Advisors – Media &amp; Impact</title>
<link rel="stylesheet" href="https://fonts.googleapis.com/css2?family=Poppins:wght@400;600;700&family=Montserrat:wght@400;500&display=swap">
<style>
  :root {
    --brand-blue: #3d8bd0;
    --ink: #111111;
    --white: #ffffff;
    --footer-dark: #262730;
    --pattern-grey: #f1f1f1;
    --muted: #d6d7db;
    --hero-top: #5b6f4a;
    --hero-bottom: #4a4037;
  }
  * { box-sizing: border-box; margin: 0; padding: 0; }
  html, body { width: 950px; height: 1200px; overflow: hidden; background: var(--white); }
  body { position: relative; font-family: "Poppins", sans-serif; color: var(--ink); }

  .site-header {
    position: absolute; left: 0; top: 0; width: 950px; height: 98px;
    background: var(--brand-blue);
  }
  .brand {
    position: absolute; display: flex; align-items: center; gap: 12px;
    font-family: "Montserrat", sans-serif; font-weight: 500; color: var(--white);
    text-transform: uppercase;
  }
  .brand-mark { width: 12px; height: 12px; background: currentColor; flex: none; }
  .brand-name { line-height: 1.05; }
  .site-header .brand { left: 114px; top: 14px; font-size: 17px; letter-spacing: 5px; }

  .cta {
    position: absolute; left: 582px; top: 16px; width: 254px; height: 34px;
    border: 2px solid var(--white); color: var(--white);
    font-size: 10.5px; font-weight: 700; text-transform: uppercase;
    display: flex; align-items: center; justify-content: center;
  }
  .main-nav a {
    position: absolute; top: 70px; color: var(--white); text-decoration: none;
    font-size: 11px; font-weight: 700; text-transform: uppercase; white-space: nowrap;
  }
  .main-nav a.current { border-bottom: 1.5px solid var(--white); padding-bottom: 1px; }

  .hero {
    position: absolute; left: 0; top: 98px; width: 950px; height: 440px;
    background: linear-gradient(180deg, var(--hero-top) 0%, #6b6a55 45%, var(--hero-bottom) 100%);
  }
  .hero-edge { position: absolute; left: 0; top: 440px; display: block; }

  .section-title {
    position: absolute; left: 0; width: 950px; top: 505px; text-align: center;
    font-size: 26px; font-weight: 700;
  }
  .title-rule { position: absolute; left: 464px; top: 546px; width: 22px; height: 3px; background: var(--brand-blue); }

  .podcast-card {
    position: absolute; top: 601px; width: 347px; height: 282px; overflow: hidden;
  }
  .podcast-card .media { position: absolute; inset: 0; }
  .card-left { left: 113px; }
  .card-left .media { background: radial-gradient(circle at 60% 40%, #6a4a35 0%, #2a1a12 45%, #0b0806 100%); }
  .card-right { left: 487px; }
  .card-right .media { background: linear-gradient(180deg, #e8e6e2 0%, #9f958f 40%, #7b736c 70%, #4b4a46 100%); }
  .podcast-card .mic { position: absolute; left: 22px; top: 166px; }
  .podcast-card h3 {
    position: absolute; left: 22px; right: 10px; top: 236px;
    color: var(--white); font-size: 11.5px; font-weight: 700; line-height: 1.25; text-transform: uppercase;
  }
  .card-right .mic { left: 16px; }
  .card-right h3 { left: 13px; }

  .pattern-band {
    position: absolute; left: 0; top: 890px; width: 950px; height: 145px;
    background: var(--pattern-grey);
  }
  .footer-shape { position: absolute; left: 0; top: 945px; display: block; }
  .site-footer {
    position: absolute; left: 0; top: 1030px; width: 950px; height: 170px;
    background: var(--footer-dark); color: var(--white);
  }
  .site-footer .brand { left: 113px; top: 30px; font-size: 22px; letter-spacing: 6px; }
  .footer-divider { position: absolute; left: 483px; top: 16px; width: 1px; height: 112px; background: #4a4b55; }
  .footer-menu-label { position: absolute; left: 530px; top: 30px; font-size: 10px; font-weight: 700; }
  .footer-links {
    position: absolute; left: 530px; top: 57px; font-size: 9.5px; font-weight: 400; color: var(--muted);
    white-space: nowrap; display: flex; gap: 8px;
  }
  .copyright { position: absolute; left: 531px; top: 106px; font-size: 9px; color: var(--muted); font-family: "Montserrat", sans-serif; }
</style>
</head>
<body>
  <header class="site-header">
    <div class="brand"><span class="brand-mark"></span><span class="brand-name">Brightwater<br>Civic<br>Advisors</span></div>
    <a class="cta">Book a Complimentary Consultation</a>
    <nav class="main-nav">
      <a style="left:445px">About</a>
      <a style="left:507px">Services &amp; Testimonials</a>
      <a class="current" style="left:667px">Media &amp; Impact</a>
      <a style="left:782px">Contact</a>
    </nav>
  </header>

  <section class="hero" role="img" aria-label="Group photo of students and volunteers standing together in a campus garden"></section>
  <svg class="hero-edge" width="950" height="100" viewBox="0 0 950 100">
    <polygon points="0,92 476,18 950,100 0,100" fill="var(--white)"/>
    <polygon points="0,84 476,10 950,92 950,100 476,18 0,92" fill="var(--brand-blue)"/>
  </svg>

  <h2 class="section-title">Podcasts</h2>
  <div class="title-rule"></div>

  <article class="podcast-card card-left">
    <div class="media" role="img" aria-label="Speaker at a podium addressing volunteers"></div>
    <svg class="mic" width="40" height="56" viewBox="0 0 40 56" fill="none" stroke="#fff" stroke-width="4">
      <rect x="10" y="2" width="20" height="32" rx="10" fill="#fff" stroke="none"/>
      <path d="M4 22 v4 a16 16 0 0 0 32 0 v-4"/>
      <path d="M20 42 v10 M10 53 h20"/>
    </svg>
    <h3>Dana welcoming volunteers to the annual college orientation week service event</h3>
  </article>

  <article class="podcast-card card-right">
    <div class="media" role="img" aria-label="People walking across a lawn in front of a brick building"></div>
    <svg class="mic" width="40" height="56" viewBox="0 0 40 56" fill="none" stroke="#fff" stroke-width="4">
      <rect x="10" y="2" width="20" height="32" rx="10" fill="#fff" stroke="none"/>
      <path d="M4 22 v4 a16 16 0 0 0 32 0 v-4"/>
      <path d="M20 42 v10 M10 53 h20"/>
    </svg>
    <h3>Dana introducing a dinner dialogue on the intersection of education and mental health</h3>
  </article>

  <div class="pattern-band" role="img" aria-label="Faint decorative background band"></div>
  <svg class="footer-shape" width="950" height="90" viewBox="0 0 950 90">
    <polygon points="0,86 472,0 950,86 950,90 0,90" fill="var(--footer-dark)"/>
  </svg>

  <footer class="site-footer">
    <div class="brand"><span class="brand-mark"></span><span class="brand-name">Brightwater<br>Civic<br>Advisors</span></div>
    <div class="footer-divider"></div>
    <div class="footer-menu-label">MENU</div>
    <div class="footer-links">
      <span>ABOUT</span><span>|</span>
      <span>SERVICES &amp; TESTIMONIALS</span><span>|</span>
      <span>MEDIA &amp; IMPACT</span><span>|</span>
      <span>CONTACT</span>
    </div>
    <div class="copyright">Copyrights @ 2019 All Rights Reserved</div>
  </footer>
</body>
</html>
```